Packaging design for health, nutrition, essential oils, herbals, vitamins and product lines. We want an upscale design that is aligned with nature. Must add a tree graphic into the design because our products are forest or tree products.

We need boxes, bottles, tags, labels for herbs, herbal formulas, vitamin bottles,

This is the text that will be on the packaging.

Larkmere Verdant Remedies (bold this)
-- insert eclectic tree graphic ---
Aligned With Nature
Est. Aspen, Colorado

The colors of our brand are
Platinum, White, Silver, Chrome, Clear Glass
The Graphic we need is an eclectic or cool forest tree preferably pine trees or christmas trees but we are also open to an eclectic tree graphic

We also need to see a tree graphic in the branding packaging
We are opened to adding some green to the packaging as well

Our products that we need the packaging for are
Herbs and Herbal Formulas
Beverages
Fragrances
Aromatherapy
Essential Oils
Nutritional Products
Vitamins, Supplements and Minerals

It is very important to provide us with a luxury brand that compliments our firm, Larkmere Clinicians.
This is a new division of our firm that delivers all
100% ALL NATURAL PLANT BASED PRODUCTS and INDIGENOUS MEDICINES

I love the idea of having
platinum or shiny silver contrast against minimalist white and or glass and a must have is to add green (forest or herbal green color) and a tree graphic

Again : Our products are all forest and plant based

We also will have the same designer create a web page for the commerce store after this project

Target Market(s)

Luxury Consumers, Plant Based Medicine and Natural Healing Consumers, Herbs and Herbal Formula Consumers, Health Conscious Consumers, Nature or Environmental Products Consumers, High Networth Consumers

Industry/Entity Type

Health Product

Requirements
Must have
• Colors : Platinum, Silver, Chrome, White and A Tree or Plant Leaves Graphic, Preferably a Forest Tree
• Maintain same font as our LarkmereClinicians.com logo brand
Should not have
• No other colors besides white, platinum, silver, chrome or forest or tree green

```html
<!DOCTYPE html>
<html lang="en">
<head>
<meta charset="utf-8">
<title>Larkmere Verdant Remedies — Box Lid and Insert</title>
<link rel="stylesheet" href="https://fonts.googleapis.com/css2?family=Tinos:wght@400;700&family=Open+Sans:wght@400&display=swap">
<style>
  :root {
    --page: #ffffff;
    --lid: #f6f6f4;
    --lid-edge: #e4e5e2;
    --silver-dark: #8e8f8f;
    --silver-light: #c9caca;
    --forest-green: #8cc63f;
    --tray: #dcdddb;
    --tray-deep: #d2d3d1;
    --tray-rim: #e8e9e7;
    --well: #ffffff;
    --well-shade: #eeeeed;
    --tray-text: #9d9e9d;
    --serif: "Tinos", "Times New Roman", serif;
    --sans: "Open Sans", Arial, sans-serif;
  }
  * { box-sizing: border-box; margin: 0; padding: 0; }
  html, body {
    width: 903px;
    height: 1200px;
    overflow: hidden;
    background: var(--page);
  }
  .canvas {
    position: relative;
    width: 903px;
    height: 1200px;
  }

  /* Box lid, shown flat */
  .box-lid {
    position: absolute;
    left: 92px;
    top: 60px;
    width: 720px;
    height: 430px;
    background: linear-gradient(160deg, #fbfbfa 0%, var(--lid) 60%, #ececea 100%);
    border: 1px solid var(--lid-edge);
    box-shadow: 0 18px 30px -18px rgba(0, 0, 0, 0.18);
    text-align: center;
    font-family: var(--serif);
  }
  .lid-brand {
    margin-top: 58px;
    font-size: 34px;
    font-weight: 700;
    letter-spacing: 0.42em;
    padding-left: 0.42em;
    background: linear-gradient(180deg, var(--silver-light), var(--silver-dark));
    -webkit-background-clip: text;
    background-clip: text;
    color: transparent;
  }
  .lid-subbrand {
    margin-top: 6px;
    font-size: 19px;
    font-weight: 700;
    letter-spacing: 0.04em;
    color: var(--forest-green);
  }
  .lid-mark {
    display: block;
    margin: 30px auto 0;
  }
  .lid-tagline {
    margin-top: 36px;
    font-size: 20px;
    font-weight: 700;
    color: var(--forest-green);
    letter-spacing: 0.02em;
  }
  .lid-origin {
    margin-top: 6px;
    font-size: 13px;
    color: var(--silver-dark);
    letter-spacing: 0.06em;
  }

  /* Product insert tray */
  .insert-tray {
    position: absolute;
    left: 80px;
    top: 672px;
    width: 731px;
    height: 450px;
    background: linear-gradient(180deg, var(--tray-rim) 0%, var(--tray) 18%, var(--tray) 82%, var(--tray-deep) 100%);
    box-shadow: inset 0 0 0 1px rgba(255, 255, 255, 0.5), 0 16px 28px -16px rgba(0, 0, 0, 0.22);
  }
  .tray-brand {
    position: absolute;
    left: 0;
    right: 0;
    top: 8px;
    text-align: center;
    font-family: var(--serif);
    font-weight: 700;
    font-size: 33px;
    line-height: 38px;
    letter-spacing: 0.5em;
    padding-left: 0.5em;
    background: linear-gradient(180deg, #b9baba, #979898);
    -webkit-background-clip: text;
    background-clip: text;
    color: transparent;
  }
  .tray-powered {
    position: absolute;
    right: 181px;
    top: 47px;
    font-family: var(--serif);
    font-size: 12px;
    line-height: 14px;
    color: #9a9b9a;
    letter-spacing: 0.01em;
  }
  .product-well {
    position: absolute;
    background: linear-gradient(180deg, var(--well-shade) 0%, var(--well) 14%, var(--well) 100%);
    box-shadow:
      inset 0 3px 6px rgba(0, 0, 0, 0.10),
      inset 0 0 0 1px rgba(0, 0, 0, 0.04),
      0 1px 0 rgba(255, 255, 255, 0.8);
  }
  .well-tall-wide { left: 43px;  top: 65px; width: 224px; height: 337px; }
  .well-tall-slim { left: 309px; top: 68px; width: 145px; height: 330px; }
  .well-square    { left: 495px; top: 70px; width: 194px; height: 212px; }
  .well-short     { left: 495px; top: 322px; width: 194px; height: 76px; }
  .tray-footer {
    position: absolute;
    left: 0;
    right: 0;
    top: 418px;
    text-align: center;
    font-family: var(--sans);
    font-size: 18px;
    line-height: 24px;
    color: var(--tray-text);
  }
</style>
</head>
<body>
<main class="canvas">
  <section class="box-lid">
    <h1 class="lid-brand">LARKMERE</h1>
    <p class="lid-subbrand">VERDANT REMEDIES</p>
    <svg class="lid-mark" width="96" height="96" viewBox="0 0 96 96" aria-hidden="true">
      <defs>
        <linearGradient id="chrome" x1="0" y1="0" x2="1" y2="1">
          <stop offset="0" stop-color="#d9dada"/>
          <stop offset="0.5" stop-color="#a4a5a5"/>
          <stop offset="1" stop-color="#cfd0d0"/>
        </linearGradient>
      </defs>
      <circle cx="48" cy="48" r="44" fill="url(#chrome)"/>
    </svg>
    <p class="lid-tagline">ALIGNED WITH NATURE</p>
    <p class="lid-origin">EST. ASPEN, COLORADO</p>
  </section>

  <section class="insert-tray">
    <h2 class="tray-brand">LARKMERE</h2>
    <p class="tray-powered">POWERED BY PHYTONCIDES</p>
    <div class="product-well well-tall-wide"></div>
    <div class="product-well well-tall-slim"></div>
    <div class="product-well well-square"></div>
    <div class="product-well well-short"></div>
    <p class="tray-footer">Phytocide Infused Products</p>
  </section>
</main>
</body>
</html>
```